Transform Your Giving

I need a tri-fold brochure that will fit in a standard number 10 business envelope. Meadowlark and Allied Services is a charitable nonprofit. The goal of this brochure is to stimulate people into thinking about other ways to make a donation. The design should communicate the essential information on donation options, create a sense of professional integrity, be graphically sharp, easy to read and laid out in a way that doesn't make the material appear crowded.

```html
<!DOCTYPE html>
<html lang="en">
<head>
<meta charset="utf-8">
<title>Transform Your Giving – Meadowlark and Allied Services</title>
<link href="https://fonts.googleapis.com/css2?family=Montserrat:wght@600;700;800;900&family=Open+Sans:wght@400;600;700&display=swap" rel="stylesheet">
<style>
:root{
  --forest:#17573a;
  --leaf:#7cc242;
  --leaf-soft:#e8f4dc;
  --ink:#2b2b2b;
  --muted:#555;
  --paper:#ffffff;
  --canvas:#ffffff;
}
*{box-sizing:border-box;margin:0;padding:0}
html,body{width:758px;height:1200px;overflow:hidden;background:var(--canvas)}
body{font-family:"Open Sans",Arial,sans-serif;color:var(--ink);position:relative}
.sheet{position:absolute;left:6px;width:746px;background:var(--paper);box-shadow:0 0 0 1px #ddd;overflow:hidden}
.sheet.outside{top:8px;height:620px}
.sheet.inside{top:642px;height:550px}
.panel{position:absolute;top:0;bottom:0;width:248.7px;overflow:hidden}
.p1{left:0}.p2{left:248.7px}.p3{left:497.4px}
h2,h3,h4{font-family:"Montserrat",Arial,sans-serif}
p{font-size:7.2px;line-height:1.45;color:var(--muted);margin-bottom:5px}
.sub{color:var(--leaf);font-family:"Montserrat",sans-serif;font-weight:700;font-size:8.5px;margin-bottom:5px}
.how{font-family:"Montserrat",sans-serif;font-weight:800;font-size:8.5px;color:var(--forest);margin:6px 0 3px}
.photo{position:absolute}
/* outside */
.impact-photo{left:10px;top:10px;width:228px;height:200px;border-radius:0 0 130px 0;background:linear-gradient(135deg,#c9d8c2,#7a8f76 60%,#4f6a52)}
.ring{position:absolute;left:-30px;top:-40px;width:300px;height:268px;border:8px solid var(--leaf);border-top:none;border-left:none;border-radius:0 0 170px 0}
.impact{position:absolute;left:16px;top:244px;right:14px}
.impact h3{font-size:12.5px;color:var(--forest);font-weight:800;margin-bottom:6px}
.impact p{font-size:7.6px}
.checklist{list-style:none;margin-top:10px}
.checklist li{font-size:8.2px;font-weight:700;color:var(--forest);display:flex;align-items:center;gap:7px;padding:6px 0;border-bottom:1px solid #e3e3e3}
.checklist li::before{content:"";width:9px;height:9px;border-radius:50%;background:var(--leaf);flex:none}
.site-band{position:absolute;left:0;right:0;bottom:0;height:40px;background:var(--forest);color:#fff;font-family:"Montserrat",sans-serif;font-weight:700;font-size:10px;display:flex;align-items:center;padding-left:20px;border-top:4px solid var(--leaf)}
.mid{position:absolute;left:16px;right:16px;top:18px;text-align:center}
.mid p{font-size:7.6px;margin-bottom:7px}
.mid .web{font-family:"Montserrat",sans-serif;font-weight:800;font-size:13px;color:var(--forest);margin:8px 0}
.contact{margin-top:18px;padding-top:14px;border-top:2px solid var(--leaf)}
.contact h3{font-size:14px;font-weight:900;color:var(--forest);margin-bottom:4px}
.contact .line{font-size:8px;font-weight:700;color:var(--ink);margin:6px 0;display:flex;justify-content:center;align-items:center;gap:5px}
.contact .fine{margin-top:12px;font-size:6px}
.curve-mid{position:absolute;left:0;right:0;bottom:0;height:80px}
.cover{background:var(--forest);color:#fff}
.cover-photo{left:0;right:0;top:136px;height:170px;background:linear-gradient(135deg,#a7b9a0,#5f7560 55%,#344b38)}
.cover .titles{position:absolute;left:18px;right:14px;top:22px;text-align:center}
.cover h2{font-weight:900;font-size:16px;line-height:1.12}
.cover h2 .g{color:var(--leaf)}
.cover .tag{font-size:7.8px;line-height:1.4;margin-top:8px}
.icons{position:absolute;left:14px;right:14px;top:330px;display:flex;flex-wrap:wrap;justify-content:center;gap:12px 16px}
.icon{width:52px;text-align:center;font-size:7px;font-weight:700}
.icon span{display:block;width:34px;height:34px;margin:0 auto 4px;border-radius:50%;background:#fff;border:3px solid var(--leaf)}
.brand{position:absolute;left:0;right:0;bottom:50px;text-align:center;font-family:"Montserrat",sans-serif;font-weight:900;font-size:24px;color:#fff;display:flex;justify-content:center;align-items:center;gap:7px}
.brand i{width:16px;height:16px;background:var(--leaf);border-radius:50%}
.brand-sub{position:absolute;left:0;right:0;bottom:32px;text-align:center;font-size:7px}
/* inside */
.col{position:absolute;left:14px;right:12px;top:14px}
.sec-title{font-size:12px;font-weight:800;color:var(--forest);line-height:1.2}
.inside-photo{border-radius:8px}
.divider{height:3px;background:var(--leaf);margin:9px 0;width:60px}
.green-box{background:var(--leaf-soft);border-left:3px solid var(--leaf);padding:6px 7px;margin:5px 0}
.dot{display:inline-block;width:22px;height:22px;border-radius:50%;background:var(--leaf);vertical-align:middle;margin-right:6px;flex:none}
.row{display:flex;align-items:center;margin-bottom:5px}
.footer-band{position:absolute;left:0;right:0;bottom:0;height:16px;background:var(--forest);border-top:3px solid var(--leaf)}
</style>
</head>
<body>

<section class="sheet outside">
  <div class="panel p1">
    <div class="ring"></div>
    <div class="photo impact-photo" role="img" aria-label="Photo of a smiling donor holding a gift box"></div>
    <div class="impact">
      <h3>THE IMPACT OF YOUR GIFT</h3>
      <p>Your generosity drives our mission. With every smart gift you choose, you help Meadowlark and Allied Services deliver care and support to those who need it most. Giving strategically can increase your impact while offering benefits to you. Begin your smart giving journey with us today.</p>
      <ul class="checklist">
        <li>Stocks and Securities</li>
        <li>DAFs</li>
        <li>QCDs</li>
        <li>Crypto</li>
        <li>Charitable Annuity</li>
      </ul>
    </div>
    <div class="site-band">www.meadowlarkallied.org</div>
  </div>

  <div class="panel p2">
    <div class="mid">
      <p>To learn more about Smart Giving Options and how they can benefit you and Meadowlark and Allied Services, please reach out to our dedicated team. We are here to help you navigate these giving methods and answer any question you may have.</p>
      <p>Being able to share is good for your heart!</p>
      <p style="margin-top:10px">If you do not have a will, go to</p>
      <div class="web">www.easywillhub.org</div>
      <p>In 20 minutes you can have a legal will – FOR FREE.</p>
      <div class="contact">
        <h3>CONTACT US</h3>
        <p>Have more questions? Please contact us at Meadowlark and Allied Services</p>
        <div class="line">555-014-2200 (ext. 110)</div>
        <div class="line">hello@meadowlarkallied.org</div>
        <p class="fine">This material has been prepared for informational purposes only and is not intended to provide tax, accounting or legal advice. Meadowlark and Allied Services recommends consulting a qualified advisor before acting on any strategy described.</p>
      </div>
    </div>
    <svg class="curve-mid" viewBox="0 0 249 80" preserveAspectRatio="none" aria-hidden="true">
      <path d="M0 46 Q120 14 249 34 L249 80 L0 80Z" fill="#17573a"/>
      <path d="M0 46 Q120 14 249 34" fill="none" stroke="#7cc242" stroke-width="4"/>
    </svg>
  </div>

  <div class="panel p3 cover">
    <div class="photo cover-photo" role="img" aria-label="Photo of a couple reviewing their giving plans together"></div>
    <div class="titles">
      <h2>TRANSFORM <span class="g">YOUR GIVING</span><br>BE STRATEGIC<br><span class="g">BE SMART</span></h2>
      <div class="tag">Discover the Impact of Smart Giving with Meadowlark and Allied Services</div>
    </div>
    <div class="icons">
      <div class="icon"><span></span>Crypto</div>
      <div class="icon"><span></span>DAFs</div>
      <div class="icon"><span></span>Stocks &amp; Securities</div>
      <div class="icon"><span></span>QCDs</div>
      <div class="icon"><span></span>Charitable Annuity</div>
    </div>
    <div class="brand"><i></i>MAAS</div>
    <div class="brand-sub">Meadowlark and Allied Services</div>
  </div>
</section>

<section class="sheet inside">
  <div class="panel p1">
    <div class="col">
      <p>We would like to introduce you to five Strategic and Smart ways to give that could potentially be more beneficial to you compared to traditional cash donations. We encourage you to take this brochure as a guide to your future contributions.</p>
      <div class="divider"></div>
      <h3 class="sec-title">Gifts of Stocks or Appreciated Assets</h3>
      <div class="sub">Strategic &amp; Smart</div>
      <div class="row"><span class="dot"></span><p style="margin:0">Consider gifting your long-term publicly traded stock as a way to give to your favorite charity.</p></div>
      <p>You can make a significantly bigger impact when you donate long-term appreciated assets, including stocks, mutual funds and bonds, directly to your favorite charity.</p>
      <div class="how">How Does It Work?</div>
      <p>When you donate stock to a charity, you will generally take a tax deduction for the full market value. Because you are donating the asset rather than selling it first, there may be a significant tax benefit from transferring the shares directly to the charity.</p>
      <p>The charity, being tax exempt, can then sell the asset without owing capital gains. The entire value goes to the cause you care about, and you avoid paying tax on the gain.</p>
      <div class="green-box"><p style="margin:0">Speak with your broker about transferring shares to Meadowlark and Allied Services. Our team will provide account details on request.</p></div>
      <p>The more your asset has grown, the greater the potential benefit. Many donors find this one of the simplest smart gifts.</p>
      <div class="how">Why Give Stock?</div>
      <p>It stretches your giving budget, supports programs that serve the community and lets your investments do good twice.</p>
    </div>
    <div class="footer-band"></div>
  </div>

  <div class="panel p2">
    <div class="col">
      <h3 class="sec-title">Donor-Advised Fund (DAF)</h3>
      <div class="sub">Strategic &amp; Smart</div>
      <div class="row">
        <div class="photo inside-photo" style="position:relative;width:90px;height:68px;flex:none;margin-right:7px;background:linear-gradient(135deg,#cfe0c4,#7fa56e)" role="img" aria-label="Photo of hands holding a small plant"></div>
        <p style="margin:0">Consider a DAF – a simple, flexible and tax-advantaged way to give to your favorite charities.</p>
      </div>
      <p>A donor advised fund (DAF) is like a charitable investment account for the sole purpose of supporting your favorite charities.</p>
      <div class="how">How Does It Work?</div>
      <p>You can contribute to a DAF with cash, stocks or non-publicly traded assets. Contributions are generally eligible for an immediate tax deduction. The assets can grow tax free, and you can recommend grants to any qualified charity over time.</p>
      <div class="divider"></div>
      <h3 class="sec-title">Qualified Charitable Distributions (QCDs)</h3>
      <div class="sub">Strategic &amp; Smart</div>
      <div class="row"><span class="dot"></span><p style="margin:0">Consider a QCD when planning your IRA withdrawal strategy – and donate directly to your favorite charity.</p></div>
      <p>We know at age 70 ½ a rule was created to allow you to give from your IRA to a charity. These transfers count toward your required minimum distribution and are not included in your taxable income.</p>
      <div class="how">How Does It Work?</div>
      <p>Ask your IRA administrator to send a Qualified Charitable Distribution directly to Meadowlark and Allied Services. The amount can satisfy all or part of your required distribution for the year, up to the annual limit set by law.</p>
      <div class="green-box"><p style="margin:0">Be sure the check is made payable to the charity, not to you, to keep the gift qualified.</p></div>
    </div>
    <div class="footer-band"></div>
  </div>

  <div class="panel p3">
    <div class="col">
      <div class="row"><span class="dot"></span><div><h3 class="sec-title">CRYPTOCURRENCY</h3><div class="sub" style="margin:0">Strategic &amp; Smart</div></div></div>
      <p>Consider donating Bitcoin and other cryptocurrencies to your favorite charity.</p>
      <p>Bitcoin and other cryptocurrencies can be donated in similar fashion to other appreciated assets such as stocks. Gifts of crypto held longer than a year can be deducted at full market value.</p>
      <div class="how">How Does It Work?</div>
      <p>• Your tax deduction will be based on the fair market value at the time you donate.</p>
      <p>• Your cryptocurrency donation is tax exempt because it may eliminate capital gains taxes on the asset. Appreciation stays with the cause.</p>
      <p>Often charities can not take or accept direct donations of digital tokens, so using a DAF is a great way to make the gift.</p>
      <div class="divider"></div>
      <div class="row"><span class="dot"></span><div><h3 class="sec-title">CHARITABLE GIFT ANNUITY</h3><div class="sub" style="margin:0">Strategic &amp; Smart</div></div></div>
      <p>Consider establishing a Charitable Gift Annuity for income now and a legacy later.</p>
      <p>A charitable gift annuity is a contract between a donor and a charity. In return for a gift of cash or securities, the charity agrees to pay you fixed income for life.</p>
      <div class="how">How Does It Work?</div>
      <p>Your gift is transferred to the charity, and you receive a partial tax deduction for your contribution. Payments are based on your age and are partially tax free. When the annuity ends, the remaining balance supports Meadowlark and Allied Services.</p>
      <div class="green-box"><p style="margin:0">A gift annuity can provide dependable income while creating a lasting legacy for the community you love.</p></div>
    </div>
    <div class="footer-band"></div>
  </div>
</section>

</body>
</html>
```